Coastline Premier Retreats Business Card Design

Design a business card for Coastline Premier Retreats. Look at the website for colors and reference. Card should have logo, name, title, office number, mobile number, email, URL and a tagline like, "Luxury Hotel & Resort Email Marketing" (This might change).

https://www.coastlinepremierretreats.example

The rest I will leave up to your imagination.

Contact Information for Business Card

Logo, name, title, office number, mobile number, email, URL and a tagline like, "Luxury Hotel & Resort Email Marketing" (This might change).

```html
<!DOCTYPE html>
<html lang="en">
<head>
<meta charset="utf-8">
<title>Coastline Premier Retreats – Business Card</title>
<link href="https://fonts.googleapis.com/css2?family=Open+Sans:wght@400;600;700&display=swap" rel="stylesheet">
<style>
  :root {
    --backdrop: #232323;
    --paper: #fdfdf6;
    --orange: #f37321;
    --ink: #111111;
    --white: #ffffff;
  }
  * { box-sizing: border-box; margin: 0; padding: 0; }
  html, body { width: 1200px; height: 780px; overflow: hidden; }
  body {
    background: var(--backdrop);
    font-family: "Open Sans", Arial, sans-serif;
    position: relative;
  }
  .card {
    position: absolute;
    width: 540px;
    height: 310px;
    background: var(--paper);
    border-radius: 18px;
    overflow: hidden;
    top: 235px;
  }
  .card--front { left: 40px; }
  .card--back { left: 620px; }

  .card__wave { position: absolute; inset: 0; width: 540px; height: 310px; }

  .brand {
    position: absolute;
    display: flex;
    align-items: center;
    gap: 8px;
    color: var(--ink);
    font-weight: 700;
    text-transform: uppercase;
    white-space: nowrap;
  }
  .brand__square { background: var(--orange); flex: none; }
  .card--front .brand { top: 30px; right: 30px; font-size: 13px; letter-spacing: 0.4px; }
  .card--front .brand__square { width: 11px; height: 11px; }
  .card--back .brand {
    top: 50%; left: 50%; transform: translate(-50%, -50%);
    font-size: 25px; letter-spacing: 1px; gap: 12px;
  }
  .card--back .brand__square { width: 18px; height: 18px; }

  .person { position: absolute; top: 54px; left: 40px; }
  .person__name { font-size: 24px; font-weight: 700; color: var(--ink); line-height: 1.1; white-space: nowrap; }
  .person__first { color: var(--orange); }
  .person__title { font-size: 15px; color: var(--ink); margin-top: 4px; padding-left: 22px; }

  .divider {
    position: absolute; left: 206px; top: 122px;
    width: 2px; height: 84px; background: var(--ink);
  }
  .contacts {
    position: absolute; left: 222px; top: 120px;
    list-style: none; font-size: 12.5px; color: var(--ink);
  }
  .contacts li { display: flex; align-items: center; gap: 8px; height: 22px; white-space: nowrap; }
  .contacts svg { width: 12px; height: 12px; flex: none; }

  .tagline {
    position: absolute; left: 40px; bottom: 14px;
    font-size: 14px; color: var(--white);
  }
</style>
</head>
<body>

<section class="card card--front" aria-label="Business card front">
  <svg class="card__wave" viewBox="0 0 540 310" aria-hidden="true">
    <path d="M0,218 C40,258 140,270 260,272 C380,274 470,264 540,254 L540,310 L0,310 Z" fill="var(--orange)"/>
    <path d="M22,204 C70,250 170,262 280,262 C390,262 470,252 520,246" fill="none" stroke="var(--ink)" stroke-width="3" stroke-linecap="round"/>
  </svg>

  <div class="brand"><span class="brand__square"></span>Coastline Premier Retreats</div>

  <div class="person">
    <p class="person__name"><span class="person__first">Marta</span> Velinska</p>
    <p class="person__title">Managing Director</p>
  </div>

  <div class="divider"></div>

  <ul class="contacts">
    <li>
      <svg viewBox="0 0 16 16" aria-hidden="true"><path d="M3 1h3l1.5 4-2 1.3a9 9 0 0 0 4.2 4.2L11 8.5l4 1.5v3a2 2 0 0 1-2 2A12 12 0 0 1 1 3a2 2 0 0 1 2-2z" fill="var(--orange)"/></svg>
      (555) 014-2758
    </li>
    <li>
      <svg viewBox="0 0 16 16" aria-hidden="true"><rect x="4" y="1" width="8" height="14" rx="1.5" fill="none" stroke="var(--orange)" stroke-width="1.6"/></svg>
      (555) 014-7777
    </li>
    <li>
      <svg viewBox="0 0 16 16" aria-hidden="true"><circle cx="8" cy="8" r="7" fill="var(--orange)"/><path d="M1 8h14M8 1c-3 3-3 11 0 14M8 1c3 3 3 11 0 14" fill="none" stroke="var(--paper)" stroke-width="1"/></svg>
      www.coastlinepremierretreats.example
    </li>
    <li>
      <svg viewBox="0 0 16 16" aria-hidden="true"><rect x="1" y="3" width="14" height="10" rx="1" fill="var(--orange)"/><path d="M1.5 3.5 8 9l6.5-5.5" fill="none" stroke="var(--paper)" stroke-width="1.2"/></svg>
      info@coastlinepremierretreats.example
    </li>
  </ul>

  <p class="tagline">Luxury Hotel &amp; Resort Email Marketing</p>
</section>

<section class="card card--back" aria-label="Business card back">
  <div class="brand"><span class="brand__square"></span>Coastline Premier Retreats</div>
</section>

</body>
</html>
```